Header/Banner Design for Website

Looking for a banner/header design for www.nestfixerdiaries.net Should be fun and whimsical, and include the name of the website, something to do with Nest Fixer Diaries or tools, and a caricature of a young, beautiful 20 something blond who the website revolves around. The website is about a young woman who bought her first house and it taking on all of the renovations and remodeling on her own for the first time.

The header/banner should include the same colors that are in the website. The width should be no more than 430 pixels, the height is flexible but the current space in the header is 85 pixels...looking for some creativity. any questions, please ask. Attached an image that she liked for the image of the woman (would like to see versions of this included)
Updates

Target Market(s)

women 20+ that are new home owners or that are tackling Nest Fixer Diaries on their own

Industry/Entity Type

Nest Fixer Diaries

Requirements
Must have
• color coordinate with the website
should feature a young, blond, female caricature
should include the name of the website

```html
<!DOCTYPE html>
<html lang="en">
<head>
<meta charset="utf-8">
<title>Nest Fixer Diaries – Completed Projects</title>
<link rel="stylesheet" href="https://fonts.googleapis.com/css2?family=Oswald:wght@400;500&family=Roboto+Condensed:ital,wght@0,400;0,700;1,700&display=swap">
<style>
  :root {
    --room-light: #efe9e2;
    --room-warm: #d9c7b1;
    --header-pink: #f2a9cb;
    --header-pink-deep: #e27fb0;
    --nav-plum: #6d1a47;
    --nav-active: #c12a76;
    --page-pink: #f9cfe1;
    --panel-cream: #f1e3c4;
    --panel-pink: #f9d3e4;
    --magenta: #d7247a;
    --plum-box: #7c2050;
    --free-red: #d11d2a;
    --ink: #1d1d1d;
    --white: #ffffff;
    --status-grey: #dcdcdc;
  }
  * { box-sizing: border-box; margin: 0; padding: 0; }
  html, body { width: 1200px; height: 900px; overflow: hidden; }
  body {
    position: relative;
    font-family: "Roboto Condensed", Arial, sans-serif;
    color: var(--ink);
  }
  .room-backdrop {
    position: absolute; inset: 0;
    background: linear-gradient(90deg, var(--room-light) 0%, #f6f2ec 40%, var(--room-warm) 100%);
  }
  .site {
    position: absolute; left: 143px; top: 57px; width: 900px; height: 843px;
    border-radius: 12px 12px 0 0; overflow: hidden;
    background: var(--page-pink);
  }
  .site-header {
    position: absolute; left: 0; top: 0; width: 900px; height: 135px;
    background: linear-gradient(180deg, #f7c3dc 0%, var(--header-pink) 60%, var(--header-pink-deep) 100%);
  }
  .brand {
    position: absolute; left: 16px; top: 38px;
    display: flex; align-items: center; gap: 10px;
    font-family: "Oswald", sans-serif; font-weight: 500;
    font-size: 38px; color: var(--nav-plum); letter-spacing: 0.5px;
  }
  .brand-dot { width: 16px; height: 16px; border-radius: 50%; background: var(--magenta); }
  .mascot {
    position: absolute; left: 367px; top: 3px; width: 230px; height: 132px;
    background: linear-gradient(135deg, #c97fd6 0%, #e89ac6 55%, #f4c1db 100%);
  }
  .search { position: absolute; left: 605px; top: 50px; display: flex; }
  .search-field {
    width: 180px; height: 42px; border-radius: 6px 0 0 6px;
    background: #f9d0e3; padding-left: 6px;
    font-size: 15px; color: #7b6a72;
    display: flex; align-items: center;
  }
  .search-button {
    width: 102px; height: 52px; margin-top: -4px; border-radius: 6px;
    background: var(--nav-active); color: var(--white);
    font-family: "Oswald", sans-serif; font-size: 19px;
    display: flex; align-items: center; justify-content: center; gap: 4px;
  }
  .main-nav {
    position: absolute; left: 0; top: 135px; width: 900px; height: 65px;
    background: var(--nav-plum); display: flex; padding-left: 20px;
  }
  .main-nav a {
    color: var(--white); text-decoration: none;
    font-family: "Oswald", sans-serif; font-weight: 500; font-size: 17.5px;
    display: flex; align-items: center; padding: 0 22px; height: 65px;
  }
  .main-nav a.is-active { background: var(--nav-active); padding: 0 20px; }
  .video-frame {
    position: absolute; left: 17px; top: 239px; width: 560px; height: 523px;
    background: var(--white); border-radius: 6px;
  }
  .video-player {
    position: absolute; left: 10px; top: 15px; width: 538px; height: 492px;
    background: #000; border: 2px solid #4b5a66; border-radius: 4px;
  }
  .feature-card {
    position: absolute; top: 793px; height: 60px; background: #f1e1d0; border-radius: 4px;
  }
  .sidebar {
    position: absolute; left: 597px; top: 237px; width: 287px; height: 620px;
    background: var(--panel-cream); border-radius: 4px;
  }
  .guide-panel {
    position: absolute; left: 12px; top: 44px; width: 263px; height: 580px;
    background: linear-gradient(90deg, var(--white) 0%, var(--white) 62%, var(--panel-pink) 85%);
    overflow: hidden;
  }
  .guide-title {
    position: absolute; left: 9px; top: 22px;
    font-family: "Oswald", sans-serif; font-weight: 500; font-size: 22px; color: var(--magenta);
  }
  .guide-box {
    position: absolute; left: 25px; top: 76px; width: 213px; height: 108px;
    background: linear-gradient(180deg, #a24275 0%, var(--plum-box) 100%);
    border: 2px solid #5a1338; border-radius: 4px;
    text-align: center; padding-top: 13px;
    font-family: "Oswald", sans-serif; font-weight: 500; font-size: 18px; line-height: 27px; color: var(--white);
  }
  .guide-box .accent { color: #f05aa0; }
  .guide-bonus {
    position: absolute; left: 0; top: 190px; width: 263px; text-align: center;
    font-style: italic; font-weight: 700; font-size: 15px; line-height: 28px;
  }
  .guide-bonus .free {
    font-family: "Oswald", sans-serif; font-style: normal; font-weight: 400;
    font-size: 24px; line-height: 1; color: var(--free-red);
  }
  .guide-pack {
    position: absolute; left: 53px; top: 250px; width: 145px; height: 130px;
    background: linear-gradient(135deg, #c75a9a 0%, #e9a9cb 60%, #8d8d8d 100%);
  }
  .signup { position: absolute; left: 0; top: 396px; width: 263px; }
  .field-row { position: absolute; display: flex; align-items: center; }
  .field-row label { font-style: italic; font-size: 16px; width: 46px; text-align: right; margin-right: 12px; }
  .field-row .input { width: 142px; height: 29px; background: var(--white); border: 1px solid #a7a7a7; }
  .download {
    position: absolute; left: 77px; top: 98px; width: 144px; height: 33px;
    background: linear-gradient(180deg, #ee4b97 0%, var(--magenta) 100%);
    border-radius: 5px; color: var(--white);
    font-family: "Oswald", sans-serif; font-size: 17px;
    display: flex; align-items: center; justify-content: center;
  }
  .status-bar {
    position: absolute; left: 0; top: 873px; width: 396px; height: 27px;
    background: var(--status-grey); border: 1px solid #b5b5b5; border-left: none;
    font-family: Arial, sans-serif; font-size: 13px; color: #333;
    display: flex; align-items: center; padding-left: 2px;
  }
</style>
</head>
<body>
  <div class="room-backdrop" role="img" aria-label="Photo of a bright room under renovation, opening onto a finished living space"></div>

  <div class="site">
    <header class="site-header">
      <div class="brand"><span class="brand-dot"></span>Nest Fixer Diaries</div>
      <div class="mascot" role="img" aria-label="Cartoon illustration of a young blond woman on a pink bubbly backdrop"></div>
      <div class="search">
        <div class="search-field">Search</div>
        <div class="search-button">Search
          <svg width="14" height="14" viewBox="0 0 14 14"><circle cx="6" cy="6" r="4" fill="none" stroke="#fff" stroke-width="2"/><line x1="9" y1="9" x2="13" y2="13" stroke="#fff" stroke-width="2"/></svg>
        </div>
      </div>
    </header>

    <nav class="main-nav">
      <a href="#">About Us</a>
      <a href="#">Products</a>
      <a href="#" class="is-active">Completed Projects</a>
      <a href="#">Share Your Project</a>
      <a href="#">Articles</a>
      <a href="#">How to Resources</a>
    </nav>

    <div class="video-frame"><div class="video-player"></div></div>
    <div class="feature-card" style="left:9px;width:275px"></div>
    <div class="feature-card" style="left:297px;width:275px"></div>

    <aside class="sidebar">
      <div class="guide-panel" role="img" aria-label="Sign-up panel with a soft pink decorative backdrop">
        <div class="guide-title">A FREE GUIDE</div>
        <div class="guide-box">10 QUESTIONS <span class="accent">TO ASK<br>BEFORE HIRING A</span><br>CONTRACTOR</div>
        <div class="guide-bonus">Receive Bonus How-to Videos and<br>Instructions All <span class="free">FREE</span></div>
        <div class="guide-pack" role="img" aria-label="Guide booklet with two bonus DVDs"></div>
        <div class="signup">
          <div class="field-row" style="left:20px;top:0"><label>Name:</label><div class="input"></div></div>
          <div class="field-row" style="left:20px;top:48px"><label>Email:</label><div class="input"></div></div>
          <div class="download">Download Now</div>
        </div>
      </div>
    </aside>
  </div>

  <div class="status-bar">www.nestfixerdiaries.net/completed-projects/</div>
</body>
</html>
```